Business Card and Letterhead for Pimlu - modern real estate business

I need a double sided business card design for Pimlu. Please see business card brief here https://files.trelvonadocs.com/sheet/r/7QzTmWbaXLJnoPEd-kRyUgFhHsstbvCe2qfoMxDa_pz/view?mode=shared

Please feel free to design the business cards however you feel best. I am happy to give some creative freedoms and then provide feedback from there.

Please then also create a letterhead to match the business card design

Colors

Designer to choose colors to be used in the design.

Requirements
Must have
• Must be a modern, elegant business card which looks very professional

```html
<!DOCTYPE html>
<html lang="en">
<head>
<meta charset="utf-8">
<title>Pimlu – Business Card</title>
<link rel="stylesheet" href="https://fonts.googleapis.com/css2?family=Lato:wght@300;400&family=Raleway:wght@700;800&display=swap">
<style>
  :root {
    --ink: #161616;
    --paper: #f1f1f1;
    --page: #ffffff;
    --brand-red: #e5202a;
    --text-light: #e4e4e4;
    --text-dark: #2b2b2b;
  }
  * { margin: 0; padding: 0; box-sizing: border-box; }
  html, body {
    width: 1200px; height: 1000px; overflow: hidden;
    background: var(--page);
  }
  .card {
    position: absolute; left: 100px; top: 190px;
    width: 1000px; height: 620px;
    background: var(--ink);
    overflow: hidden;
  }
  .card__paper {
    position: absolute; left: 0; top: 0;
    width: 1000px; height: 620px;
  }
  .portrait-frame {
    position: absolute; left: 33px; top: 58px;
    width: 327px; height: 504px;
    background: var(--brand-red);
    border: 2px solid #222;
  }
  .portrait {
    position: absolute; left: 15px; top: 18px;
    width: 293px; height: 466px;
    border: 2px solid #1a1a1a;
    background: linear-gradient(180deg, #c9d3d6 0%, #8a9a80 28%, #6b7a5a 40%, #3a3a3c 55%, #262628 100%);
  }
  .agent {
    position: absolute; left: 388px; top: 50px;
    color: var(--text-light);
  }
  .agent__name, .agent__title {
    font-family: "Raleway", sans-serif;
    font-weight: 700; font-size: 29px; line-height: 38px;
    color: #ffffff;
  }
  .agent__detail {
    font-family: "Lato", sans-serif;
    font-weight: 300; font-size: 30px; line-height: 39px;
    letter-spacing: 0.3px;
  }
  .brand-name {
    position: absolute; left: 414px; top: 292px;
    font-family: "Raleway", sans-serif;
    font-weight: 800; font-size: 112px; line-height: 120px;
    letter-spacing: 6px;
    color: var(--brand-red);
  }
  .office {
    position: absolute; top: 424px;
    font-family: "Lato", sans-serif;
    font-weight: 300; font-size: 30px; line-height: 38px;
    color: var(--text-dark);
  }
  .office--left { left: 388px; }
  .office--right { left: 731px; }
</style>
</head>
<body>
  <div class="card">
    <svg class="card__paper" viewBox="0 0 1000 620" aria-hidden="true">
      <path fill="#f1f1f1" d="M0 318 L362 318 L362 268 L372 272 L384 266 L396 275 L410 269 L424 276 L438 270 L452 273 L468 267 L482 274 L500 270 L516 276 L534 268 L552 273 L570 271 L588 277 L606 270 L624 274 L640 268 L660 276 L678 272 L696 278 L716 270 L734 275 L752 269 L770 276 L790 272 L804 280 L820 274 L838 279 L856 271 L872 277 L890 274 L908 284 L926 278 L944 286 L962 280 L980 290 L1000 286 L1000 620 L0 620 Z"/>
    </svg>

    <div class="portrait-frame">
      <div class="portrait" role="img" aria-label="Portrait photo of the agent in a dark suit, outdoors with a valley view behind"></div>
    </div>

    <div class="agent">
      <p class="agent__name">Liam Harper</p>
      <p class="agent__title">Licenced Real Estate Agent</p>
      <p class="agent__detail">Lic No. 20381946</p>
      <p class="agent__detail">0412 309 884</p>
      <p class="agent__detail">liam@pimlu.com</p>
    </div>

    <p class="brand-name">PIMLU</p>

    <div class="office office--left">
      <p>Lic No. 10047218</p>
      <p>PO Box 1736</p>
      <p>Bralston NSW 2790</p>
      <p>02 4861 3527</p>
    </div>
    <div class="office office--right">
      <p>info@pimlu.com</p>
      <p>www.pimlu.com</p>
    </div>
  </div>
</body>
</html>
```